Exciting & Elegant Stationary Pack

Stationary consists of
1. Letter head / Envelope
2. Business Card
3. Invoice
4. 40x40mm sticker

Attached files;

1. Logo (Other formats available on request)
2. MS word Doc - For information and description of design
3. Website image (This will be our new website so use the colours so everything ties together)
4. Sample of stationary pack we like, but feel free to be creative

Target Market(s)

Home improvement

Industry/Entity Type

Construction

Font styles to use
Other font styles liked:
• Leave up to designer - We like font used on (website attached image)

Requirements
Must have
• Please look at uploaded file of sample website and use colours
Nice to have
• Any type of business card design - eg. metal, die cut, embossed, etc...

```html
<!DOCTYPE html>
<html lang="en">
<head>
<meta charset="utf-8">
<title>Setline Tiling – Stationery Pack</title>
<link rel="stylesheet" href="https://fonts.googleapis.com/css2?family=Open+Sans:wght@400;600;700;800&display=swap">
<style>
:root{
  --navy:#1d4a6e;
  --navy-deep:#163c5a;
  --red:#cc2a32;
  --sky:#9cc3e3;
  --paper:#f1f0ee;
  --stage:#a9a7a8;
  --ink:#333a40;
  --stripe:#c9cfd6;
}
*{box-sizing:border-box;margin:0;padding:0}
html,body{width:1200px;height:838px;overflow:hidden}
body{background:var(--stage);font-family:"Open Sans",Arial,sans-serif;color:var(--ink);position:relative}
.piece{position:absolute;background:var(--paper);box-shadow:0 2px 6px rgba(0,0,0,.25);overflow:hidden}
.band-red{position:absolute;left:0;right:0;background:var(--red)}
.band-sky{position:absolute;left:0;right:0;background:var(--sky)}
.brand{position:absolute;font-weight:800;color:var(--navy);letter-spacing:.5px;white-space:nowrap;line-height:1}
.icon{display:inline-block;vertical-align:-1px;margin-right:2px}
.contact-line{position:absolute;left:0;right:0;font-size:7px;color:var(--ink);text-align:center;white-space:nowrap}
.abn{position:absolute;right:18px;font-size:6.5px;color:#fff}

/* folder */
.folder{left:42px;top:50px;width:378px;height:531px;background:linear-gradient(160deg,#22537a,var(--navy) 60%,var(--navy-deep))}
.folder .band-red{top:433px;height:49px}
.folder .band-sky{top:482px;height:49px}
.folder .brand{left:18px;top:372px;font-size:34px;color:#fff}

/* letterhead + invoice header */
.sheet{top:91px;width:348px;height:490px}
.letterhead{left:435px}
.invoice{left:807px}
.sheet .brand{left:28px;top:32px;font-size:16px}
.sheet .band-red{top:59px;height:20px}
.sheet .band-sky{top:79px;height:22px}
.sheet .abn{top:66px}
.sheet .contact-line{top:86px}

.letter-body{position:absolute;left:26px;right:26px;top:140px;font-size:4.6px;line-height:1.85;color:#555}
.letter-body .salutation{font-size:8.5px;color:var(--ink);margin-bottom:20px}
.letter-body p{margin-bottom:8px;text-align:justify}
.sign-off{margin-top:16px}
.signature{display:block;margin:6px 0 2px 10px}
.signer{margin-left:13px;line-height:1.9}

/* invoice form */
.field{position:absolute;font-size:5.2px;color:var(--ink);display:flex;align-items:flex-end}
.field .rule{flex:1;border-bottom:.6px solid var(--navy);margin-left:3px;height:5px}
.field-label{position:absolute;font-size:5.4px;font-weight:700;color:var(--navy)}
.item-table{position:absolute;left:25px;top:172px;width:297px;border-collapse:collapse;font-size:5.4px;border:.8px solid var(--navy)}
.item-table th{background:var(--navy);color:#fff;font-weight:700;height:14px;text-align:center}
.item-table td{height:13.6px;border-left:.6px solid var(--navy)}
.item-table tr:nth-child(even) td{background:var(--stripe)}
.col-qty{width:24px}.col-price{width:39px}.col-amount{width:39px}
.totals{position:absolute;left:243px;top:413px;border-collapse:collapse;font-size:5px;font-weight:700;color:var(--navy)}
.totals td{border:.6px solid var(--navy);height:13.5px;width:39px;text-align:center;background:var(--paper)}
.pay-methods{position:absolute;left:25px;top:426px;font-size:5.4px;font-weight:600;word-spacing:16px}
.bank-details{position:absolute;left:25px;top:440px;font-size:6.8px;line-height:1.45}

/* business cards */
.card-front{left:46px;top:595px;width:152px;height:86px;background:#fff}
.card-front .brand{left:8px;top:19px;font-size:9px}
.card-front .band-red{top:39px;height:15px}
.card-front .band-sky{top:54px;bottom:0}
.card-name{position:absolute;right:8px;top:41px;text-align:right;color:#fff;font-size:5.2px;font-weight:700;line-height:1.2}
.card-name small{display:block;font-size:3.4px;font-weight:400}
.card-details{position:absolute;right:8px;top:60px;text-align:right;font-size:3.8px;line-height:1.55;color:var(--ink)}
.card-back{left:42px;top:694px;width:153px;height:87px;background:var(--navy)}
.card-back .texture{position:absolute;inset:0;background:linear-gradient(135deg,#1f4f75,#183f5e)}
.card-back .brand{right:10px;top:42px;font-size:9px;color:#fff}

/* envelopes */
.env-front{left:211px;top:604px;width:391px;height:177px}
.env-front .brand{left:24px;top:24px;font-size:14px}
.env-front .band-red{top:50px;height:20px}
.env-front .band-sky{top:70px;height:21px}
.env-front .contact-line{top:77px;left:27px;text-align:left}
.env-back{left:614px;top:606px;width:391px;height:178px}
.env-flap{position:absolute;left:0;right:0;top:0;height:56px;background:var(--navy);border-radius:0 0 10px 10px}
.env-back .brand{left:50%;transform:translateX(-50%);top:17px;font-size:10px;color:#fff}

/* sticker */
.sticker{left:1025px;top:623px;width:157px;height:157px;background:#fff}
.sticker .brand{left:14px;top:54px;font-size:13px}
.sticker .band-red{top:84px;height:23px}
.sticker .band-sky{top:107px;bottom:0}
.sticker-details{position:absolute;right:10px;top:125px;text-align:right;font-size:6.5px;line-height:1.6;color:var(--ink)}
</style>
</head>
<body>

<!-- presentation folder -->
<section class="piece folder" aria-label="Presentation folder">
  <div class="brand">SETLINE TILING</div>
  <div class="band-red"></div>
  <div class="band-sky"></div>
</section>

<!-- letterhead -->
<section class="piece sheet letterhead" aria-label="Letterhead">
  <div class="brand">SETLINE TILING</div>
  <div class="band-red"></div>
  <div class="band-sky"></div>
  <div class="abn">ABN : 12 345 678 901</div>
  <div class="contact-line">
    <svg class="icon" width="5" height="7" viewBox="0 0 10 14"><path d="M5 0a5 5 0 0 0-5 5c0 4 5 9 5 9s5-5 5-9a5 5 0 0 0-5-5zm0 7a2 2 0 1 1 0-4 2 2 0 0 1 0 4z" fill="#222"/></svg>PO Box 48 Riverbend NSW 2170
    <svg class="icon" width="7" height="5" viewBox="0 0 14 10"><rect width="14" height="10" fill="#222"/><path d="M0 0l7 5 7-5" stroke="#9cc3e3" fill="none"/></svg>info@setlinetiling.com.au
    <svg class="icon" width="6" height="6" viewBox="0 0 10 10"><circle cx="5" cy="5" r="5" fill="#222"/></svg>www.setlinetiling.com.au
  </div>
  <div class="letter-body">
    <div class="salutation">Dear Mr. Harlow,</div>
    <p>Thank you for choosing us for your bathroom renovation. This letter confirms the scope of work agreed during our site visit, including removal of existing tiles, waterproofing of wet areas and installation of new floor and wall tiles throughout the room.</p>
    <p>Our team will arrive on the agreed start date and keep the work area clean and safe each day. Materials will be delivered in advance, and any changes to the tile selection can be discussed before cutting begins.</p>
    <p>All work is carried out by licensed tradespeople and is covered by our workmanship warranty. Once the job is complete we will walk through the finished space with you and make sure every joint, edge and fall meets your expectations.</p>
    <p>If you have any questions before we begin, please call or email us at any time.</p>
    <div class="sign-off">Sincerely,</div>
    <svg class="signature" width="50" height="16" viewBox="0 0 50 16"><path d="M2 10 C12 6 30 4 48 8 M12 4 C18 2 22 6 18 10 C16 13 28 14 34 10" stroke="#222" stroke-width=".8" fill="none"/></svg>
    <div class="signer">Peter Harlow<br>CEO/ Founder</div>
  </div>
</section>

<!-- invoice -->
<section class="piece sheet invoice" aria-label="Invoice">
  <div class="brand">SETLINE TILING</div>
  <div class="band-red"></div>
  <div class="band-sky"></div>
  <div class="abn">ABN : 12 345 678 901</div>
  <div class="contact-line">
    <svg class="icon" width="5" height="7" viewBox="0 0 10 14"><path d="M5 0a5 5 0 0 0-5 5c0 4 5 9 5 9s5-5 5-9a5 5 0 0 0-5-5zm0 7a2 2 0 1 1 0-4 2 2 0 0 1 0 4z" fill="#222"/></svg>PO Box 48 Riverbend NSW 2170
    <svg class="icon" width="7" height="5" viewBox="0 0 14 10"><rect width="14" height="10" fill="#222"/><path d="M0 0l7 5 7-5" stroke="#9cc3e3" fill="none"/></svg>info@setlinetiling.com.au
    <svg class="icon" width="6" height="6" viewBox="0 0 10 10"><circle cx="5" cy="5" r="5" fill="#222"/></svg>www.setlinetiling.com.au
  </div>
  <div class="field-label" style="left:25px;top:123px">INVOICE # :</div>
  <div class="field-label" style="left:248px;top:123px">DATE :</div>
  <div class="field" style="left:26px;right:26px;top:137px">Customer:<span class="rule"></span></div>
  <div class="field" style="left:26px;right:26px;top:149px">Address :<span class="rule"></span></div>
  <div class="field" style="left:26px;width:150px;top:162px">Phone :<span class="rule"></span></div>
  <div class="field" style="left:178px;right:26px;top:162px">Email :<span class="rule"></span></div>
  <table class="item-table">
    <thead><tr><th class="col-qty">QTY</th><th>DESCRIPTION</th><th class="col-price">PRICE</th><th class="col-amount">AMOUNT</th></tr></thead>
    <tbody>
      <tr><td></td><td></td><td></td><td></td></tr><tr><td></td><td></td><td></td><td></td></tr>
      <tr><td></td><td></td><td></td><td></td></tr><tr><td></td><td></td><td></td><td></td></tr>
      <tr><td></td><td></td><td></td><td></td></tr><tr><td></td><td></td><td></td><td></td></tr>
      <tr><td></td><td></td><td></td><td></td></tr><tr><td></td><td></td><td></td><td></td></tr>
      <tr><td></td><td></td><td></td><td></td></tr><tr><td></td><td></td><td></td><td></td></tr>
      <tr><td></td><td></td><td></td><td></td></tr><tr><td></td><td></td><td></td><td></td></tr>
      <tr><td></td><td></td><td></td><td></td></tr><tr><td></td><td></td><td></td><td></td></tr>
      <tr><td></td><td></td><td></td><td></td></tr><tr><td></td><td></td><td></td><td></td></tr>
    </tbody>
  </table>
  <table class="totals">
    <tr><td>SUB TOTAL</td><td></td></tr>
    <tr><td>GST # 10%</td><td></td></tr>
    <tr><td>SUBTOTAL</td><td></td></tr>
  </table>
  <div class="pay-methods">PAYPAL CASH BANK</div>
  <div class="bank-details">Account name: Setline Tiling<br>BSB: 000-111<br>Account # : 1234 5678</div>
</section>

<!-- business card front -->
<section class="piece card-front" aria-label="Business card front">
  <div class="brand">SETLINE TILING</div>
  <div class="band-red"></div>
  <div class="band-sky"></div>
  <div class="card-name">Dana Whitlock<small>Project Manager</small></div>
  <div class="card-details">Lic No.100234c<br>0400 555 123 ▯<br>info@setlinetiling.com.au ■<br>www.setlinetiling.com.au ●</div>
</section>

<!-- business card back -->
<section class="piece card-back" aria-label="Business card back">
  <div class="texture" role="img" aria-label="Navy tile-grid texture"></div>
  <div class="brand">SETLINE TILING</div>
</section>

<!-- envelope front -->
<section class="piece env-front" aria-label="Envelope front">
  <div class="brand">SETLINE TILING</div>
  <div class="band-red"></div>
  <div class="band-sky"></div>
  <div class="contact-line">
    <svg class="icon" width="5" height="7" viewBox="0 0 10 14"><path d="M5 0a5 5 0 0 0-5 5c0 4 5 9 5 9s5-5 5-9a5 5 0 0 0-5-5zm0 7a2 2 0 1 1 0-4 2 2 0 0 1 0 4z" fill="#222"/></svg>PO Box 48 Riverbend NSW 2170
  </div>
</section>

<!-- envelope back -->
<section class="piece env-back" aria-label="Envelope back">
  <div class="env-flap"></div>
  <div class="brand">SETLINE TILING</div>
</section>

<!-- sticker -->
<section class="piece sticker" aria-label="40x40mm sticker">
  <div class="brand">SETLINE TILING</div>
  <div class="band-red"></div>
  <div class="band-sky"></div>
  <div class="sticker-details">0400 555 123 ▯<br>PO Box 48 Riverbend NSW 2170 ●</div>
</section>

</body>
</html>
```